BrightLedgerMoney(.com) needs website & logo design

We need our website mock-up made into a reality! We are wanting to launch a multifaceted website for all things financial - i.e. blogs, financial wellness information, and a network of redirect links.
We have an existing mock-up, which I will include, but are open to your creative approach!

Industry/Entity Type

Finance

Coding

Coded - Design and coding required

Number of Pages Required

1 page

Requirements
Must have
• Corresponding logo

```html
<!DOCTYPE html>
<html lang="en">
<head>
<meta charset="utf-8">
<title>Bright Ledger Money</title>
<link href="https://fonts.googleapis.com/css2?family=Poppins:wght@600;700&family=Roboto:wght@400;500;700&display=swap" rel="stylesheet">
<style>
:root{
  --teal:#72d9c0;
  --purple:#9b85c5;
  --purple-dark:#6a559f;
  --purple-light:#c9b9e4;
  --ink:#222;
  --body:#666;
  --pale:#f4f4f4;
  --white:#fff;
}
*{margin:0;padding:0;box-sizing:border-box}
html,body{width:1200px;height:3906px;overflow:hidden}
body{position:relative;background:var(--white);font-family:'Roboto',sans-serif;color:var(--ink)}
.abs{position:absolute}
h1,h2{font-family:'Poppins',sans-serif;font-weight:700}
.logo{font-family:'Poppins',sans-serif;font-weight:600;color:var(--purple);font-size:22px;line-height:26px}
.btn{position:absolute;display:flex;align-items:center;justify-content:center;background:var(--purple);color:var(--white);border-radius:22px;font-size:13px;font-weight:500;text-transform:uppercase}

/* header + hero */
.hero-bg{left:0;top:0;width:1200px;height:686px;background:var(--pale)}
.nav a{position:absolute;top:36px;font-size:14px;font-weight:500;color:var(--ink);text-decoration:none}
.nav a.active{color:var(--teal);border-bottom:2px solid var(--teal);padding-bottom:4px}
.hero-art{left:546px;top:83px;width:654px;height:584px;border-radius:50% 40% 45% 50%;background:radial-gradient(circle at 55% 50%,#5d8fc9 0%,#9fc2e6 45%,rgba(244,244,244,0) 72%)}
.hero-title{left:110px;top:210px;width:560px;font-size:44px;line-height:52px;color:var(--ink)}
.hero-text{left:111px;top:325px;width:420px;font-size:14px;line-height:26px;color:var(--body)}
.signup{left:111px;top:389px;font-size:25px;font-weight:500;color:var(--purple)}
.email{left:111px;top:437px;width:381px;height:42px;border:1px solid #ddd;border-radius:22px;background:var(--white);font-size:13px;color:#555;padding:12px 24px}

/* feature strip */
.strip{left:0;top:686px;width:1200px;height:177px;display:flex}
.tile{width:200px;height:177px;display:flex;flex-direction:column;align-items:center;justify-content:center;color:var(--white);font-size:21px;font-weight:500;gap:16px}
.tile.a{background:linear-gradient(90deg,var(--purple-dark),var(--purple-light))}
.tile.b{background:var(--purple)}
.tile svg{width:64px;height:64px;fill:none;stroke:var(--white);stroke-width:2.2}

/* trending */
.trend-bg{left:0;top:863px;width:1200px;height:584px;background:var(--pale)}
.trend-title{left:620px;top:962px;font-size:41px;line-height:52px}
.trend-text{left:620px;width:468px;font-size:14px;line-height:26px;color:var(--body);text-align:justify}

/* topic cards */
.card{position:absolute;width:309px;height:178px;background:var(--teal);border-radius:4px;display:flex;flex-direction:column;align-items:center;justify-content:center;gap:14px;color:var(--white);font-weight:700;font-size:20px}
.card svg{width:70px;height:70px;fill:var(--white)}

/* wellness band */
.band{left:0;top:2031px;width:1200px;height:460px;background:linear-gradient(180deg,#a592c8,#9a84c2 70%,#b0a0d0)}
.band-title{left:0;width:1200px;top:2136px;text-align:center;color:var(--white);font-size:42px}
.band-text{left:205px;width:790px;top:2201px;text-align:center;color:var(--white);font-size:14px;line-height:26px}

/* blog */
.blog-title{left:0;width:1200px;top:2582px;text-align:center;font-size:40px}
.post{position:absolute;top:2667px;width:309px;text-align:center}
.post .photo{height:209px;border-radius:4px}
.post .tag{display:inline-block;margin-top:24px;background:#e6f8f2;border-radius:14px;padding:6px 20px;font-size:12px}
.post h3{margin-top:14px;font-size:21px;font-weight:500}
.post p{margin-top:8px;font-size:14px;line-height:26px;color:var(--body);padding:0 22px}
.arrow{position:absolute;top:2856px;width:44px;height:44px;border-radius:50%;background:#e4e4e4;display:flex;align-items:center;justify-content:center}
.arrow svg{width:16px;height:16px;fill:none;stroke:var(--ink);stroke-width:2}

/* questions */
.q-title{left:0;width:1200px;top:3249px;text-align:center;color:var(--white);font-size:40px}
.q-text{left:190px;width:820px;top:3314px;text-align:center;color:var(--white);font-size:14px;line-height:26px}

/* footer */
.foot-head{top:3608px;font-size:20px;font-weight:500}
.foot-about{left:205px;top:3682px;width:270px;font-size:14px;line-height:26px;color:var(--body)}
.links{left:564px;top:3655px;list-style:none;font-size:14px;line-height:26px;color:var(--body)}
.contact-row{position:absolute;left:796px;display:flex;gap:18px;font-size:14px;line-height:26px;color:var(--body)}
.contact-row svg{width:16px;height:16px;margin-top:5px;fill:var(--teal);flex:none}
.copy{left:0;width:1200px;top:3850px;text-align:center;font-size:14px;color:var(--body)}
</style>
</head>
<body>

<div class="abs hero-bg"></div>
<div class="abs logo" style="left:111px;top:20px">Bright Ledger<br>Money</div>
<nav class="nav">
  <a class="active" style="left:523px">Home</a>
  <a style="left:592px">About Us</a>
  <a style="left:681px">Services</a>
  <a style="left:766px">Blog</a>
  <a style="left:824px">Contact Us</a>
</nav>
<div class="btn" style="left:940px;top:26px;width:148px;height:40px">Get a Quote</div>

<div class="abs hero-art" role="img" aria-label="Splash of water shaped like a dollar sign"></div>
<h1 class="abs hero-title">A Clear Path to<br>Financial Wellness</h1>
<p class="abs hero-text">Lorem ipsum dolor sit amet, consectetur adipiscing elit, sed do tempor incididunt ut labore et dolore magna aliqua.</p>
<div class="abs signup">Signup for Free</div>
<div class="abs email">Your Email</div>
<div class="btn" style="left:111px;top:491px;width:141px;height:42px">Get Started</div>

<div class="abs strip">
  <div class="tile a"><svg viewBox="0 0 64 64"><circle cx="32" cy="22" r="12"/><path d="M32 14v16M28 18h6a3 3 0 0 1 0 6h-4a3 3 0 0 0 0 6h6"/><path d="M4 46l14-6h14l4 4H20M36 44l18-8 4 4-22 14H4"/></svg>Save</div>
  <div class="tile b"><svg viewBox="0 0 64 64"><path d="M34 6a24 24 0 0 1 24 24H34z"/><path d="M30 12a24 24 0 1 0 24 24H30z"/></svg>Budget</div>
  <div class="tile a"><svg viewBox="0 0 64 64"><rect x="14" y="4" width="36" height="56" rx="4"/><rect x="20" y="10" width="24" height="10"/><path d="M20 28h6v6h-6zM29 28h6v6h-6zM38 28h6v6h-6zM20 38h6v6h-6zM29 38h6v6h-6zM38 38h6v6h-6zM20 48h6v6h-6zM29 48h6v6h-6zM38 48h6v6h-6z"/></svg>Calculate</div>
  <div class="tile b"><svg viewBox="0 0 64 64"><path d="M6 58h52M10 58V42h8v16M26 58V34h8v16M42 58V26h8v32"/><path d="M14 30l14-12 12 8 16-16"/><circle cx="56" cy="10" r="3"/></svg>Track</div>
  <div class="tile a"><svg viewBox="0 0 64 64"><rect x="6" y="8" width="36" height="48"/><path d="M12 48V36h6v12M22 48V28h6v20"/><circle cx="40" cy="24" r="14"/><path d="M50 34l10 12"/></svg>Research</div>
  <div class="tile b"><svg viewBox="0 0 64 64"><path d="M32 34V14M32 14c-8-10-18-6-18-6s2 12 18 6zM32 14c8-10 18-6 18-6s-2 12-18 6z"/><circle cx="32" cy="42" r="10"/><path d="M4 52l14-6h10M36 52l18-8 4 4-20 12H4"/></svg>Invest</div>
</div>

<div class="abs trend-bg"></div>
<svg class="abs" style="left:159px;top:948px" width="380" height="400" viewBox="0 0 380 400">
  <path d="M197 4A196 196 0 0 0 197 396V376A176 176 0 0 1 197 24z" fill="var(--teal)"/>
</svg>
<div class="abs" role="img" aria-label="Senior couple reviewing finances together at a laptop" style="left:179px;top:967px;width:354px;height:354px;border-radius:50%;background:radial-gradient(circle at 50% 40%,#c9a483,#8c6b57 55%,#5f7fb3)"></div>
<h2 class="abs trend-title">Trending in 2021:<br>Financial Literacy</h2>
<p class="abs trend-text" style="top:1075px">Lorem ipsum dolor sit amet, consectetur adipiscing elit, sed do eiusmod tempor incididunt ut labore et dolore magna aliqua. Ut enim ad minim veniam, quis nostrud exercitation ullamco laboris nisi ut aliquip ex ea commodo consequat. Duis aute irure dolor in reprehenderit in voluptate velit esse cillum dolore eu fugiat nulla pariatur.</p>
<p class="abs trend-text" style="top:1229px">Excepteur sint occaecat cupidatat non proident, sunt in culpa qui officia deserunt mollit anim id est laborum. Lorem ipsum dolor sit amet, consectetur adipiscing elit, sed do eiusmod tempor incididunt ut labore et dolore magna aliqua.</p>

<div class="card" style="left:111px;top:1550px"><svg viewBox="0 0 64 64"><path fill-rule="evenodd" d="M32 4a28 28 0 1 0 28 28h-6A22 22 0 1 1 32 10zM32 16a16 16 0 1 0 16 16h-6A10 10 0 1 1 32 22z"/><circle cx="32" cy="32" r="4"/><path d="M34 30L52 12l2-8 6 2-2 6-6 2-16 18z"/></svg>Set Goals</div>
<div class="card" style="left:446px;top:1550px"><svg viewBox="0 0 64 64"><ellipse cx="24" cy="12" rx="18" ry="7"/><path d="M6 18c4 5 32 5 36 0v8c-4 5-32 5-36 0zM6 30c4 5 32 5 36 0v8c-4 5-32 5-36 0zM6 42c4 5 24 5 28 2v8c-4 3-24 3-28-2z"/><circle cx="46" cy="44" r="16"/><path d="M46 34v20M42 38h6a3 3 0 0 1 0 6h-4a3 3 0 0 0 0 6h6" stroke="var(--teal)" stroke-width="3" fill="none"/></svg>Money 101</div>
<div class="card" style="left:780px;top:1550px"><svg viewBox="0 0 64 64"><path d="M36 4a26 26 0 0 1 26 26H36z"/><path d="M32 10a26 26 0 1 0 26 26H32z"/></svg>Budgeting</div>
<div class="card" style="left:111px;top:1751px"><svg viewBox="0 0 64 64"><path d="M22 18L44 4l8 14z"/><rect x="4" y="20" width="56" height="36" rx="3"/><path d="M12 28h12v8H12zM10 46h6M20 46h6M30 46h6M40 46h6" stroke="var(--teal)" stroke-width="3"/></svg>Credit Mindfulness</div>
<div class="card" style="left:446px;top:1751px"><svg viewBox="0 0 64 64"><circle cx="26" cy="16" r="12"/><path d="M4 58c0-14 10-24 22-24 6 0 10 2 14 5v19z"/><circle cx="48" cy="46" r="10"/><circle cx="48" cy="46" r="4" fill="var(--teal)"/><path d="M45 32h6v6h-6zM45 54h6v6h-6zM34 43h6v6h-6zM56 43h6v6h-6z"/></svg>Debt Management</div>
<div class="card" style="left:780px;top:1751px"><svg viewBox="0 0 64 64"><path d="M24 4h16v6H24z"/><path fill-rule="evenodd" d="M12 8h40v54H12zM18 14v42h28V14z"/><path d="M22 48l8-8 6 4 8-12" stroke="var(--white)" stroke-width="3" fill="none"/><path d="M22 22l6 6M28 22l-6 6" stroke="var(--white)" stroke-width="3"/></svg>Retirement Planning</div>

<div class="abs band" role="img" aria-label="Silhouettes of people jumping at dusk under a purple sky"></div>
<svg class="abs" style="left:0;top:2350px" width="1200" height="150" viewBox="0 0 1200 150" preserveAspectRatio="none">
  <path d="M0 25C120 95 240 132 420 138C640 145 820 78 980 60C1080 49 1150 60 1200 78V150H0z" fill="var(--white)"/>
</svg>
<h2 class="abs band-title">Financial Wellness 101</h2>
<p class="abs band-text">Lorem ipsum dolor sit amet, consectetur adipiscing elit, sed do eiusmod tempor incididunt ut labore et dolore magna Lorem ipsum dolor sit amet, consectetur adipiscing elit, sed do eiusmod tempor incididunt ut labore et dolore magna aliqua. Ut enim ad minim veniam, quis nostrud exercitation ullamco laboris nisi ut aliquip ex ea commodo consequat. Duis aute irure dolor in reprehenderit in voluptate velit esse cillum dolore eu fugiat nulla pariatur.</p>

<h2 class="abs blog-title">Latest Blog</h2>
<div class="arrow" style="left:33px"><svg viewBox="0 0 16 16"><path d="M10 3L5 8l5 5"/></svg></div>
<div class="arrow" style="left:1122px"><svg viewBox="0 0 16 16"><path d="M6 3l5 5-5 5"/></svg></div>
<article class="post" style="left:111px">
  <div class="photo" role="img" aria-label="Family discussing paperwork at a bright table" style="background:linear-gradient(135deg,#e9e2d8,#b9a58f)"></div>
  <span class="tag">by John Doe</span>
  <h3>Duis aute irure dolor</h3>
  <p>Lorem ipsum dolor sit amet, consectetur adipiscing elit, sed do eiusmod tempor incididunt ut labore et dolore</p>
</article>
<article class="post" style="left:446px">
  <div class="photo" role="img" aria-label="Older couple meeting with an advisor" style="background:linear-gradient(135deg,#d9d4cb,#8e8a84)"></div>
  <span class="tag">by John Doe</span>
  <h3>Duis aute irure dolor</h3>
  <p>Lorem ipsum dolor sit amet, consectetur adipiscing elit, sed do eiusmod tempor incididunt ut labore et dolore</p>
</article>
<article class="post" style="left:780px">
  <div class="photo" role="img" aria-label="Advisor taking notes with a client on a sofa" style="background:linear-gradient(135deg,#b7c3cc,#3f4e6a)"></div>
  <span class="tag">by John Doe</span>
  <h3>Duis aute irure dolor</h3>
  <p>Lorem ipsum dolor sit amet, consectetur adipiscing elit, sed do eiusmod tempor incididunt ut labore et dolore</p>
</article>

<svg class="abs" style="left:0;top:3115px" width="1200" height="412" viewBox="0 0 1200 412" preserveAspectRatio="none">
  <path d="M0 80C80 115 160 112 280 95C460 70 600 10 780 8C940 6 1080 40 1200 120V412H0z" fill="var(--teal)"/>
</svg>
<h2 class="abs q-title">Have any Questions?</h2>
<p class="abs q-text">Lorem ipsum dolor sit amet, consectetur adipiscing elit, sed do eiusmod tempor incididunt ut labore et dolore magna Lorem ipsum dolor sit amet, consectetur adipiscing elit, sed do eiusmod tempor incididunt ut labore et dolore</p>
<div class="btn" style="left:529px;top:3381px;width:141px;height:41px">Contact Us</div>

<footer>
  <div class="abs logo" style="left:205px;top:3608px">Bright Ledger<br>Money</div>
  <p class="abs foot-about">Lorem ipsum dolor sit amet, consectetur adipiscing elit, sed do eiusmod tempor incididunt ut labore et</p>
  <h4 class="abs foot-head" style="left:564px">Quick Links</h4>
  <ul class="abs links"><li>Home</li><li>About us</li><li>Services</li><li>Blog</li><li>Contact us</li></ul>
  <h4 class="abs foot-head" style="left:796px">Contact Us</h4>
  <div class="contact-row" style="top:3655px"><svg viewBox="0 0 16 16"><path d="M8 1a5 5 0 0 0-5 5c0 4 5 9 5 9s5-5 5-9a5 5 0 0 0-5-5zm0 7a2 2 0 1 1 0-4 2 2 0 0 1 0 4z"/></svg><span>Lorem ipsum dolor sit<br>amet, consectetur</span></div>
  <div class="contact-row" style="top:3732px"><svg viewBox="0 0 16 16"><path d="M3 1l3 3-2 2c1 2 3 4 5 5l2-2 3 3-2 3C6 14 2 10 1 3z"/></svg><span>+1 888 888 8888</span></div>
  <div class="contact-row" style="top:3783px"><svg viewBox="0 0 16 16"><path d="M1 3h14v10H1zM1 3l7 6 7-6" stroke="var(--white)" stroke-width="1"/></svg><span>info@companyname.com</span></div>
  <div class="abs copy">© Copyrights 2023 Company Name | All Rights reserved</div>
</footer>

</body>
</html>
```